Business card design for new eCommerce site focusing on integrity and strong businsess tactics

We need a business card that will stand out and be memorable. Something with color that matches our company logo colors. Think high end version of Pactivo. There are 2 logos provided. The parent company is called Amber Ledge Partners and we are presenting a new and very exciting eCommerce site called BrightHarborTrade.example.

Target Market(s)

Our target markets are in the Activities, Food and Beverage, Health and Beauty

Industry/Entity Type

Marketing

Contact Information for Business Card

We have 4 members that need cards...I will provide all info to the winner of the design contest
Business Address is
4870 West 63rd Avenue, Suite C207
Phoenix AZ 85731

Font styles to use
Serif
Sans Serif

Colors

Designer to choose colors to be used in the design.

Requirements
Must have
• The card must be memorable...should be unique in design but must exude integrity and be playful .
• I have provided several colors or our parent company...please feel free to use which ever
Nice to have
• I will leave this up to you. Feel free to use other images of your choosing that wraps around our client.....Activities, Dining, Health, Beauty
Should not have
• just dont be boring

```html
<!DOCTYPE html>
<html lang="en">
<head>
<meta charset="utf-8">
<title>BrightHarborTrade.example – Business Card</title>
<link rel="stylesheet" href="https://fonts.googleapis.com/css2?family=Jost:wght@400;500;600&display=swap">
<style>
  :root {
    --backdrop: #e9e6e1;
    --card-white: #fbfbfa;
    --brand-blue: #2b7bb1;
    --name-blue: #2c80ba;
    --leaf-green: #7dbd3a;
    --ink: #555a5e;
    --rule: #8a8d90;
    --white: #ffffff;
  }
  * { margin: 0; padding: 0; box-sizing: border-box; }
  html, body { width: 1200px; height: 960px; overflow: hidden; }
  body {
    background: var(--backdrop);
    font-family: "Jost", sans-serif;
    position: relative;
  }
  .card {
    position: absolute;
    width: 600px;
    border-radius: 22px;
  }
  .card--front {
    left: 303px; top: 131px; height: 335px;
    background: var(--card-white);
    box-shadow: 0 2px 6px rgba(0,0,0,.12);
  }
  .card--back {
    left: 299px; top: 490px; height: 342px;
    background: var(--brand-blue);
    box-shadow: 0 2px 6px rgba(0,0,0,.12);
  }

  /* front: brand block */
  .brand {
    position: absolute; right: 31px; top: 66px;
    text-align: right;
  }
  .brand__name {
    display: flex; align-items: center; justify-content: flex-end; gap: 8px;
    font-size: 22px; font-weight: 500; color: var(--leaf-green);
    line-height: 1;
  }
  .brand__dot {
    width: 14px; height: 14px; border-radius: 50%;
    background: var(--name-blue);
  }
  .brand__tagline {
    margin-top: 6px;
    font-size: 12px; letter-spacing: 1.2px; color: var(--ink);
  }

  /* front: person */
  .person { position: absolute; left: 25px; top: 193px; }
  .person__name {
    font-size: 25px; font-weight: 500; color: var(--name-blue);
    text-transform: uppercase; letter-spacing: -0.3px; line-height: 1;
  }
  .person__title {
    margin-top: 5px;
    font-size: 15px; color: var(--leaf-green); text-transform: uppercase; line-height: 1;
  }
  .divider {
    position: absolute; left: 25px; right: 31px; top: 248px;
    border-top: 1px solid var(--rule);
  }

  .contact {
    position: absolute; left: 25px; top: 259px;
    list-style: none; font-size: 14.5px; color: var(--ink);
  }
  .contact li { display: flex; align-items: center; gap: 9px; height: 19.5px; }
  .contact svg { width: 13px; height: 13px; fill: var(--name-blue); flex: none; }

  .address {
    position: absolute; right: 31px; top: 259px;
    font-style: normal; text-align: right;
    font-size: 14.5px; color: var(--ink); line-height: 19.5px;
  }

  /* back */
  .back-mark {
    position: absolute; left: 50%; top: 72px;
    width: 72px; height: 72px; margin-left: -36px;
    border: 4px solid var(--white); border-radius: 50%;
  }
  .back-name {
    position: absolute; left: 0; right: 0; top: 218px;
    text-align: center;
    font-size: 36px; font-weight: 600; color: var(--white); line-height: 1;
  }
</style>
</head>
<body>

<section class="card card--front" aria-label="Business card front">
  <div class="brand">
    <div class="brand__name"><span class="brand__dot"></span>BrightHarborTrade.example</div>
    <div class="brand__tagline">Play · Taste · Wellness · Style</div>
  </div>

  <div class="person">
    <div class="person__name">Daniel Reyes</div>
    <div class="person__title">CEO/Founder</div>
  </div>

  <div class="divider"></div>

  <ul class="contact">
    <li>
      <svg viewBox="0 0 24 24" aria-hidden="true"><path d="M6.6 10.8a15.1 15.1 0 0 0 6.6 6.6l2.2-2.2c.3-.3.7-.4 1-.2 1.1.4 2.3.6 3.6.6.6 0 1 .4 1 1V20c0 .6-.4 1-1 1A17 17 0 0 1 3 4c0-.6.4-1 1-1h3.5c.6 0 1 .4 1 1 0 1.3.2 2.5.6 3.6.1.3 0 .7-.2 1z"/></svg>
      602 555 0147
    </li>
    <li>
      <svg viewBox="0 0 24 24" aria-hidden="true"><path d="M7 1h10a2 2 0 0 1 2 2v18a2 2 0 0 1-2 2H7a2 2 0 0 1-2-2V3a2 2 0 0 1 2-2zm0 3v14h10V4zm5 15.5a1.2 1.2 0 1 0 0 2.4 1.2 1.2 0 0 0 0-2.4z"/></svg>
      480 555 0193
    </li>
    <li>
      <svg viewBox="0 0 24 24" aria-hidden="true"><path d="M2 5h20v14H2zm2 2v.5l8 5 8-5V7zm0 2.8V17h16V9.8l-8 5z"/></svg>
      daniel@brightharbortrade.example
    </li>
  </ul>

  <address class="address">
    4870 West 63rd Avenue<br>
    Suite C207, Phoenix AZ 85731<br>
    www.brightharbortrade.example
  </address>
</section>

<section class="card card--back" aria-label="Business card back">
  <div class="back-mark"></div>
  <div class="back-name">Amber Ledge Partners</div>
</section>

</body>
</html>
```